CBD AgriBusiness Verdant Trophy Business Card

We are HiTec producer of medical cannabis CBD Switzerland of high quality. Our website is alpinleaf.net, we will also revisit it graphically, the winner of this contest will be the graphic designer chosen for the new design of the website. We stand out by the skill of the team, many of our engineers we win cup cannabis. I join the current map to take as an example but to revisit completely: deletion of surname and first name, modification of funds (front / back), reorganization of text info, highlighting the address of the website. three characteristics define the business card: Professional, Class, refined. The business card must be optimized for soft-touch and selective varnish printing.

Target Market(s)

Customers and Suppliers

Industry/Entity Type

Agribusiness

Contact Information for Business Card

Logo, Tél / Whatsapp, mail, url du site : alpinleaf.net

Font styles to use
Sans Serif

Requirements
Must have
• Logo of alpinleaf.net
Nice to have
• a design that stands out well on the selective varnish
Should not have
• Last name and first name

```html
<!DOCTYPE html>
<html lang="en">
<head>
<meta charset="utf-8">
<title>alpinleaf business card</title>
<link href="https://fonts.googleapis.com/css2?family=Rubik:wght@400;500;700&display=swap" rel="stylesheet">
<style>
  :root {
    --backdrop: #a4a4a4;
    --card-dark: #5a5a5c;
    --card-light: #ffffff;
    --ink: #4a4a4c;
    --ink-soft: #666668;
    --leaf: #7cc35a;
    --white: #ffffff;
  }
  * { box-sizing: border-box; margin: 0; padding: 0; }
  html, body {
    width: 1200px; height: 930px; overflow: hidden;
    background: var(--backdrop);
    font-family: "Rubik", sans-serif;
  }
  .canvas { position: relative; width: 1200px; height: 930px; }
  .card {
    position: absolute; width: 560px; height: 320px;
    border-radius: 22px;
    box-shadow: 0 8px 20px rgba(0,0,0,0.25);
  }
  .card--front { left: 80px; top: 100px; background: var(--card-dark); }
  .card--back { left: 560px; top: 510px; background: var(--card-light); }

  .brand { position: absolute; display: flex; align-items: center; gap: 12px; }
  .brand__mark { width: 34px; height: 34px; background: var(--leaf); }
  .brand__name { font-weight: 700; font-size: 58px; letter-spacing: -1px; line-height: 1; }
  .card--front .brand { left: 60px; top: 128px; }
  .card--front .brand__name { color: var(--white); }
  .card--back .brand { left: 34px; top: 120px; }
  .card--back .brand__name { color: var(--ink); font-size: 50px; }
  .card--back .brand__mark { width: 30px; height: 30px; }

  .contact { position: absolute; left: 330px; top: 74px; color: var(--ink-soft); font-size: 13.5px; line-height: 1.55; }
  .contact__role { color: var(--leaf); font-weight: 500; font-size: 17px; text-transform: uppercase; letter-spacing: 0.3px; margin-bottom: 12px; }
  .contact__address { margin-bottom: 12px; }
  .contact__line { display: flex; align-items: center; gap: 8px; }
  .contact__line svg { width: 11px; height: 11px; flex: none; }
  .contact__accent { color: var(--leaf); }
</style>
</head>
<body>
<main class="canvas">
  <section class="card card--front" aria-label="Card front">
    <div class="brand">
      <span class="brand__mark"></span>
      <span class="brand__name">alpinleaf</span>
    </div>
  </section>

  <section class="card card--back" aria-label="Card back">
    <div class="brand">
      <span class="brand__mark"></span>
      <span class="brand__name">alpinleaf</span>
    </div>
    <div class="contact">
      <p class="contact__role">Director</p>
      <p class="contact__address">42 Fernhill Road,<br>Lindale, NZ, 4120</p>
      <p class="contact__line">
        <svg viewBox="0 0 12 12" fill="none" stroke="var(--leaf)" stroke-width="1.4"><path d="M2.5 1.5l2 2.2-1 1.2a6 6 0 0 0 3.6 3.6l1.2-1 2.2 2-1 1.5C5 10.5 1.5 7 1 2.5z"/></svg>
        +41 (0) 70 555 01 23
      </p>
      <p class="contact__line">
        <svg viewBox="0 0 12 12" fill="none" stroke="var(--leaf)" stroke-width="1.4"><rect x="3" y="1" width="6" height="10" rx="1"/></svg>
        +44 7700 900 418
      </p>
      <p class="contact__line">
        <svg viewBox="0 0 12 12" fill="none" stroke="var(--leaf)" stroke-width="1.3"><rect x="1" y="2.5" width="10" height="7"/><path d="M1 2.5l5 4 5-4"/></svg>
        office@alpinleaf.net
      </p>
      <p class="contact__line">
        <svg viewBox="0 0 12 12" fill="none" stroke="var(--leaf)" stroke-width="1.2"><circle cx="6" cy="6" r="5"/><ellipse cx="6" cy="6" rx="2.2" ry="5"/><path d="M1 6h10"/></svg>
        <span>www.<span class="contact__accent">alpinleaf</span>.net</span>
      </p>
    </div>
  </section>
</main>
</body>
</html>
```